Meridale Nutrition needs Stationary and a business card

We would like to use our current logo. The text can be moved around as needed. The stationary needs to be a 'first page' where the logo is more prominent to be impressive on higher quality paper and a second page where the logo is more subtle where there will be much more information on the page. There are 2 clinic locations which will need include name, address, phone number, fax number, web address. The business card should be single sided and contain this information also.
The design must be contemporary and sophisticated as this is a science based diet run out of a medical clinic.

Target Market(s)

People wanting to lose weight, athletes looking to optimise performance, people with arthritis or fighting cancer

Industry/Entity Type

Business

Contact Information for Business Card

must use the logo. I have attached an example card with the practice details on it. there must be space for the doctors name. Also the website www.meridalenutrition.com.au

Requirements
Must have
• the logo, the business adresses and phone numbers, the website, the doctors name and qualifications
Nice to have
• some creativity
Should not have
• Do not simply reproduce the existing card please

```html
<!DOCTYPE html>
<html lang="en">
<head>
<meta charset="utf-8">
<title>Meridale Nutrition Stationery</title>
<link href="https://fonts.googleapis.com/css2?family=Jost:wght@300;400;600&display=swap" rel="stylesheet">
<style>
  :root {
    --backdrop: #e6e7e9;
    --paper: #ffffff;
    --navy: #336699;
    --sky: #35c3f0;
    --ink-grey: #7a7f86;
    --faint: #e8ecf5;
  }
  * { box-sizing: border-box; margin: 0; padding: 0; }
  html, body { width: 1200px; height: 790px; overflow: hidden; }
  body {
    position: relative;
    background: var(--backdrop);
    font-family: "Jost", "Futura", sans-serif;
  }
  .sheet {
    position: absolute;
    top: 74px;
    width: 503px;
    height: 650px;
    overflow: hidden;
    box-shadow: 6px 6px 8px rgba(0,0,0,0.35);
  }
  .sheet svg.artwork { position: absolute; inset: 0; }
  .letterhead { left: 75px; background: var(--paper); }
  .cover { left: 621px; background: var(--navy); }

  .brand-mark {
    position: absolute; left: 21px; top: 17px;
    width: 54px; height: 54px; border-radius: 50%;
    background: var(--sky);
  }
  .brand-name {
    position: absolute; left: 90px; top: 27px;
    color: var(--navy); font-weight: 600;
    font-size: 19px; line-height: 19px; letter-spacing: 0.2px;
  }
  .brand-name span { display: block; font-size: 11px; line-height: 13px; letter-spacing: 5px; text-align: center; }

  .clinic {
    position: absolute; top: 21px;
    font-size: 9.6px; line-height: 12px; font-weight: 300; color: var(--ink-grey);
  }
  .clinic strong { display: block; font-weight: 400; color: var(--navy); }
  .clinic b { font-weight: 400; color: var(--navy); }
  .clinic-east { left: 286px; }
  .clinic-harlow { left: 391px; padding-left: 0; }
  .clinic-divider {
    position: absolute; left: 385px; top: 22px; width: 1px; height: 46px; background: var(--navy);
  }

  .footer-links {
    position: absolute; left: 0; right: 0; top: 619px;
    display: flex; justify-content: center;
    color: #fff; font-size: 9.6px; line-height: 12px; font-weight: 300;
  }
  .footer-links p { padding: 0 7px; text-align: center; }
  .footer-links p + p { border-left: 1px solid #fff; text-align: left; }

  .cover-title {
    position: absolute; left: 0; right: 0; top: 38px;
    text-align: center; color: #fff; font-weight: 600;
    font-size: 42px; line-height: 42px; letter-spacing: -0.5px;
  }
  .cover-title span { display: block; font-size: 24px; line-height: 28px; letter-spacing: 10px; padding-left: 10px; }
</style>
</head>
<body>

<section class="sheet letterhead">
  <svg class="artwork" viewBox="0 0 503 650" width="503" height="650" aria-hidden="false">
    <path d="M0 58 Q251 150 503 58" fill="none" stroke="var(--sky)" stroke-width="2.5"/>
    <path d="M0 60 Q251 142 503 60" fill="none" stroke="var(--sky)" stroke-width="0.6" opacity="0.5"/>
    <circle cx="252" cy="380" r="100" fill="var(--faint)" role="img" aria-label="Faint brand circle"/>
    <path d="M0 650 L0 640 Q251 560 503 640 L503 650 Z" fill="var(--navy)"/>
    <path d="M0 636 Q251 552 503 636" fill="none" stroke="var(--sky)" stroke-width="2"/>
  </svg>

  <div class="brand-mark"></div>
  <div class="brand-name">MERIDALE<span>NUTRITION</span></div>

  <div class="clinic clinic-east">
    <strong>Eastvale</strong>
    12-14 Linden Road<br>
    Eastvale NSW 2190<br>
    <b>T:</b> 02 5550 1847
  </div>
  <div class="clinic-divider"></div>
  <div class="clinic clinic-harlow">
    <strong>Harlow Park</strong>
    88 Carrow Street<br>
    Harlow Park NSW 2044<br>
    <b>F:</b> 02 5550 2391
  </div>

  <div class="footer-links">
    <p>Shoulder and Elbow<br>www.armjointcare.com.au</p>
    <p>Knee Surgery<br>www.kneecarecentre.com.au</p>
  </div>
</section>

<section class="sheet cover">
  <svg class="artwork" viewBox="0 0 503 650" width="503" height="650">
    <path d="M0 68 Q251 160 503 68" fill="none" stroke="#fff" stroke-width="2"/>
    <circle cx="252" cy="462" r="116" fill="var(--sky)" role="img" aria-label="Brand circle"/>
    <path d="M0 650 L0 620 Q251 560 503 620 L503 650 Z" fill="var(--sky)"/>
    <path d="M0 614 Q251 550 503 614" fill="none" stroke="#fff" stroke-width="1.5"/>
  </svg>
  <h1 class="cover-title">MERIDALE<span>NUTRITION</span></h1>
</section>

</body>
</html>
```